Local Flower Farm Needs Business Card Design

I need business cards designed for a flower farm based in Eudora, Kansas.
Business Info:
We are a local cut flower farm located in Eudora, Kansas, founded by Corinne Haldwick. What started as a passion for agriculture and search for more joy in daily life has blossomed into a small business dedicated to providing the community with beautiful, fresh, and sustainable flowers. We specialize in local, seasonal blooms, ensuring that every petal reflects the care and dedication we pour into our craft. Our mission is to deliver the highest quality flowers directly to our customers through local farmers markets and to florists who share our commitment to sustainability. Join us in celebrating the beauty of nature, one bloom at a time!
Contact Details:
Corinne Haldwick
Owner
Phone 913-555-0147
Facebook: Rosalind Thorpe Gardens
Instagram: @RosalindThorpeGardens
Website: RosalindThorpeGardens.example
Target Market(s)
Wholesale to Florists and Direct to Consumer via Farmers Market
Industry/Entity Type
Florist, Farm
Contact Information for Business Card
Name, Contact Info, Logo
Look and feel
Each slider illustrates characteristics of the customer's brand and the style your logo design should communicate.

```html
<!DOCTYPE html>
<html lang="en">
<head>
<meta charset="utf-8">
<title>Rosalind Thorpe Gardens – Business Card</title>
<link rel="stylesheet" href="https://fonts.googleapis.com/css2?family=Montserrat:wght@400;800&family=Cormorant+Garamond:wght@500&display=swap">
<style>
  :root {
    --backdrop: #1c1c1c;
    --evergreen: #0f2a2e;
    --paper: #ffffff;
    --ink: #0f2a2e;
  }
  * { margin: 0; padding: 0; box-sizing: border-box; }
  html, body { width: 1200px; height: 988px; overflow: hidden; background: var(--backdrop); }
  .canvas { position: relative; width: 1200px; height: 988px; }

  .card {
    position: absolute;
    width: 560px; height: 320px;
    border-radius: 18px;
    overflow: hidden;
  }

  /* Back side */
  .card-back { left: 40px; top: 110px; background: var(--evergreen); }
  .seal {
    position: absolute; left: 50%; top: 50%;
    width: 230px; height: 230px;
    transform: translate(-50%, -50%);
    border: 1px solid rgba(255,255,255,.85);
    border-radius: 50%;
    display: flex; align-items: center; justify-content: center;
    text-align: center;
  }
  .seal-name {
    font-family: "Cormorant Garamond", serif;
    font-weight: 500;
    color: var(--paper);
    font-size: 24px;
    letter-spacing: 3px;
    line-height: 1.25;
    text-transform: uppercase;
  }

  /* Front side */
  .card-front { left: 600px; top: 540px; background: var(--paper); color: var(--ink); }
  .brand-mark {
    position: absolute; right: 34px; top: 34px;
    width: 200px;
    font-family: "Cormorant Garamond", serif;
    font-weight: 500;
    font-size: 40px;
    line-height: 1.02;
    text-transform: uppercase;
    color: var(--ink);
    text-align: right;
  }
  .identity { position: absolute; left: 34px; top: 62px; width: 250px; }
  .identity-name {
    font-family: "Montserrat", sans-serif; font-weight: 800;
    font-size: 21px; letter-spacing: .5px; text-transform: uppercase;
  }
  .identity-rule { height: 1.5px; background: var(--ink); margin: 8px 0 6px; }
  .identity-role {
    font-family: "Montserrat", sans-serif; font-weight: 400;
    font-size: 11px; letter-spacing: 1px; text-transform: uppercase;
  }
  .identity-rule.short { width: 110px; margin-top: 6px; }

  .contacts {
    position: absolute; left: 34px; top: 158px;
    list-style: none;
    font-family: "Montserrat", sans-serif; font-size: 12.5px; line-height: 1;
  }
  .contacts li { display: flex; align-items: center; gap: 9px; margin-bottom: 8px; }
  .contacts svg { width: 12px; height: 12px; flex: none; }
  .contacts .gap { display: block; width: 10px; height: 1.5px; background: var(--ink); margin: 12px 0 14px 2px; }
  .dot { width: 11px; height: 11px; border-radius: 50%; background: var(--ink); flex: none; }
</style>
</head>
<body>
<main class="canvas">

  <section class="card card-back" aria-label="Card back">
    <div class="seal">
      <p class="seal-name">Rosalind<br>Thorpe<br>Gardens</p>
    </div>
  </section>

  <section class="card card-front" aria-label="Card front">
    <p class="brand-mark">Rosalind Thorpe Gardens</p>

    <div class="identity">
      <h1 class="identity-name">Corinne Haldwick</h1>
      <div class="identity-rule"></div>
      <p class="identity-role">Owner</p>
      <div class="identity-rule short"></div>
    </div>

    <ul class="contacts">
      <li>
        <svg viewBox="0 0 24 24" aria-hidden="true"><path fill="var(--ink)" d="M6.6 10.8a15 15 0 0 0 6.6 6.6l2.2-2.2a1 1 0 0 1 1-.25 11.4 11.4 0 0 0 3.6.6 1 1 0 0 1 1 1V20a1 1 0 0 1-1 1A17 17 0 0 1 3 4a1 1 0 0 1 1-1h3.5a1 1 0 0 1 1 1c0 1.25.2 2.45.6 3.6a1 1 0 0 1-.25 1z"/></svg>
        913-555-0147
      </li>
      <li>
        <svg viewBox="0 0 24 24" aria-hidden="true"><rect x="2" y="5" width="20" height="14" rx="1.5" fill="var(--ink)"/><path d="M3 6l9 7 9-7" stroke="#fff" stroke-width="1.6" fill="none"/></svg>
        info@RosalindThorpeGardens.example
      </li>
      <li>
        <svg viewBox="0 0 24 24" aria-hidden="true"><g fill="none" stroke="var(--ink)" stroke-width="2"><circle cx="12" cy="12" r="9.5"/><ellipse cx="12" cy="12" rx="4" ry="9.5"/><path d="M2.5 12h19"/></g></svg>
        www.RosalindThorpeGardens.example
      </li>
      <li class="gap" aria-hidden="true"></li>
      <li><span class="dot" aria-hidden="true"></span>Rosalind Thorpe Gardens</li>
      <li><span class="dot" aria-hidden="true"></span>@RosalindThorpeGardens</li>
    </ul>
  </section>

</main>
</body>
</html>
```